I work in creative/artistic projects across different mediums.
It needs to communicate creativity, style, sexy, uniqueness, individuality and sophistication.
It should not look corporate.
Colours I like are black silver gold deep purple, chocolate, orchid.
It doesn't have to make use of all these colours.
I do not like bright primary colors.
Updates

Project Deadline Extended
Reason: Still in the communication process and to allow the person enough time to finish the design. Though i should know in the next day or two. Thank you.

Target Market(s)

creatives and companies wanting to inject creativity into thier business.

Industry/Entity Type

Work

Contact Information for Business Card

Corwin Haldley
0418592036
corwin@corwinhaldley-example.com

quietgoldenhourstudio.example.au

Requirements
Should not have
• Anything corporate OR OLD FASHIONED

```html
<!DOCTYPE html>
<html lang="en">
<head>
<meta charset="utf-8">
<title>Corwin Haldley — Business Card</title>
<link rel="stylesheet" href="https://fonts.googleapis.com/css2?family=Almendra&family=Arimo&display=swap">
<style>
  :root {
    --backdrop: #141216;
    --card-ink: #140c3e;
    --pattern-glow: #24185e;
    --pattern-deep: #0e0830;
    --card-edge: #0a070c;
    --silver: #cfc9e0;
    --silver-text: #ddd8ec;
    --label-tint: rgba(200, 190, 235, 0.14);
  }
  * { box-sizing: border-box; margin: 0; padding: 0; }
  html, body {
    width: 1200px;
    height: 900px;
    overflow: hidden;
    background: var(--backdrop);
  }
  .canvas {
    width: 1200px;
    height: 900px;
    display: flex;
    align-items: center;
    justify-content: center;
  }
  .business-card {
    position: relative;
    width: 1000px;
    height: 571px;
    background: var(--card-ink);
    border: 5px solid var(--card-edge);
    overflow: hidden;
    font-family: "Arimo", Arial, sans-serif;
    color: var(--silver-text);
  }
  .dot-pattern-area {
    position: absolute;
    inset: 0;
    background:
      radial-gradient(ellipse at 30% 40%, rgba(60, 44, 130, 0.45), transparent 60%),
      radial-gradient(ellipse at 75% 70%, rgba(50, 36, 110, 0.4), transparent 55%),
      linear-gradient(160deg, var(--pattern-glow), var(--pattern-deep));
  }
  .name-label {
    position: absolute;
    left: 560px;
    top: 34px;
    width: 340px;
    height: 62px;
    background: var(--label-tint);
    display: flex;
    align-items: center;
    justify-content: center;
  }
  .name-label h1 {
    font-family: "Almendra", Georgia, serif;
    font-weight: 400;
    font-size: 36px;
    letter-spacing: 1px;
    color: var(--silver-text);
  }
  .email-echo {
    position: absolute;
    left: 290px;
    top: 150px;
    font-size: 21px;
  }
  .divider {
    position: absolute;
    height: 8px;
    background: var(--silver);
  }
  .divider--upper { left: 300px; width: 672px; top: 218px; }
  .divider--lower { left: 18px; width: 954px; top: 462px; }
  .contact-list {
    position: absolute;
    left: 60px;
    top: 258px;
    list-style: none;
  }
  .contact-item {
    display: flex;
    align-items: center;
    height: 64px;
    font-size: 23px;
  }
  .contact-item svg {
    width: 36px;
    height: 36px;
    margin-right: 36px;
    flex: none;
  }
  .social-tag {
    position: absolute;
    display: flex;
    align-items: center;
    gap: 12px;
    font-size: 21px;
    color: var(--silver-text);
  }
  .social-tag .mark {
    width: 44px;
    height: 44px;
    background: var(--silver);
    border-radius: 6px;
  }
  .social-tag--upper { right: 28px; top: 240px; }
  .social-tag--lower { left: 24px; top: 490px; }
</style>
</head>
<body>
<main class="canvas">
  <article class="business-card">
    <div class="dot-pattern-area" role="img" aria-label="Decorative pattern of soft indigo circles covering the card"></div>

    <header class="name-label"><h1>Corwin Haldley</h1></header>

    <p class="email-echo">corwin@corwinhaldley-example.com</p>

    <div class="divider divider--upper"></div>

    <div class="social-tag social-tag--upper"><span>Flitnote</span><span class="mark"></span></div>

    <ul class="contact-list">
      <li class="contact-item">
        <svg viewBox="0 0 36 36" fill="none" stroke="#ddd8ec" stroke-width="2.4">
          <rect x="4" y="9" width="28" height="18"/>
          <path d="M4 9 L18 20 L32 9 M4 27 L14 17 M32 27 L22 17"/>
        </svg>
        <span>corwin@corwinhaldley-example.com</span>
      </li>
      <li class="contact-item">
        <svg viewBox="0 0 36 36" fill="none" stroke="#ddd8ec" stroke-width="2.4">
          <rect x="10" y="3" width="16" height="30" rx="3"/>
          <path d="M10 8 H26 M10 27 H26"/>
        </svg>
        <span>0418592036</span>
      </li>
      <li class="contact-item">
        <svg viewBox="0 0 36 36" fill="none" stroke="#ddd8ec" stroke-width="2.2">
          <circle cx="18" cy="18" r="14"/>
          <ellipse cx="18" cy="18" rx="6" ry="14"/>
          <path d="M4 18 H32 M6 11 H30 M6 25 H30"/>
        </svg>
        <span>quietgoldenhourstudio.example.au</span>
      </li>
    </ul>

    <div class="divider divider--lower"></div>

    <div class="social-tag social-tag--lower"><span class="mark"></span><span>Kinfold</span></div>
  </article>
</main>
</body>
</html>
```